Kestrel Q8 Wheelchair

I need to update our web site www.kestrelq8.co.nz to make it stand out and make it user friendly and have our chair looking as awesome as it is.

Target Market(s)

All terrain wheelchair users, off-road wheelchair user, Wheelchair users.

Industry/Entity Type

Manufacturing

Number of Pages Required

3 page

Font styles to use
Sans Serif

Colors
33a6d7
85acd3
f37122
f78f20

Requirements
Must have
• Link to Facebook, work on mobile phones, any help you can offer would be great
Nice to have
• Photo of our van as supplied in photos
Should not have
• How old website has an add for a Brisklane gym which we do supply anymore and it also has myself Dale Hartwick mouth painting artist which I'd like not to be linked to our new website

```html
<!DOCTYPE html>
<html lang="en">
<head>
<meta charset="utf-8">
<title>Kestrel Q8 Wheelchair</title>
<link href="https://fonts.googleapis.com/css2?family=Bebas+Neue&family=Poppins:wght@400;500;600;700&display=swap" rel="stylesheet">
<style>
:root{
  --blue:#33a6d7;
  --blue-soft:#85acd3;
  --orange:#f37122;
  --amber:#f78f20;
  --ink:#1d1f24;
  --text:#555a62;
  --dark:#3a3d46;
  --footer:#f0f1f4;
  --line:#dcdde2;
}
*{box-sizing:border-box;margin:0;padding:0}
html,body{width:1200px;height:3851px;overflow:hidden;background:#fff}
body{position:relative;font-family:'Poppins',sans-serif;color:var(--text)}
.abs{position:absolute}
.display{font-family:'Bebas Neue',sans-serif;color:var(--ink);font-weight:400;letter-spacing:.2px}
.photo{position:absolute}
.btn{position:absolute;display:flex;align-items:center;justify-content:center;background:var(--orange);color:#fff;border-radius:30px;font-weight:700;font-size:12px;letter-spacing:.3px;text-transform:uppercase;text-decoration:none}

/* header */
.site-header{left:90px;top:30px;width:1020px;height:88px;background:#fff;box-shadow:0 8px 24px rgba(0,0,0,.08);z-index:5;display:flex;align-items:center;padding:0 28px}
.brand{display:flex;flex-direction:column}
.brand-name{font-weight:600;font-size:26px;color:var(--ink);line-height:1}
.brand-tag{font-size:8.5px;font-weight:600;color:var(--ink);margin-top:3px}
.nav{margin-left:auto;display:flex;align-items:center;gap:25px;font-size:12.5px;font-weight:500;color:var(--ink)}
.nav .contact{background:#ececec;border-radius:22px;padding:11px 23px;font-size:11.5px;font-weight:600}
.user-icon{margin-left:8px}

/* hero */
.hero-photo{left:581px;top:0;width:619px;height:747px;background:linear-gradient(180deg,#9cc4e6 0%,#cfd6da 30%,#8e8a83 60%,#b5b0a8 100%);z-index:3;box-shadow:0 30px 50px rgba(0,0,0,.18)}
.hero-title{left:90px;top:220px;font-size:60px;line-height:54px}
.hero-title .accent{color:var(--blue)}
.hero-text{left:90px;top:446px;width:390px;font-size:13.5px;line-height:21px;color:var(--ink)}
.hero-count{left:90px;top:628px;font-size:30px;font-weight:600;color:var(--ink)}
.hero-count small{font-size:13px;font-weight:500}

/* ideal for band */
.ideal-band{left:0;top:695px;width:1200px;height:490px;background:var(--blue)}
.ideal-title{left:0;top:846px;width:1200px;text-align:center;font-size:24px;color:#fff}
.dot-grid{position:absolute;display:grid;gap:17px}
.dot-grid span{width:9px;height:9px;border-radius:50%;background:#fff;display:block}
.use-card{top:895px;width:169px;height:188px;background:#fff;display:flex;flex-direction:column;align-items:center}
.use-card .icon{margin-top:26px;width:92px;height:92px;border-radius:8px;background:#e6f3fa}
.use-card .label{margin-top:28px;font-size:20px}

/* video */
.video-photo{left:160px;top:1185px;width:381px;height:509px;background:linear-gradient(180deg,#a9cde6 0%,#d5dde0 35%,#6e6458 65%,#4f463d 100%);box-shadow:0 20px 40px rgba(0,0,0,.2)}
.play{left:479px;top:1387px;width:106px;height:106px;border-radius:50%;background:var(--amber);display:flex;align-items:center;justify-content:center}
.about-title{left:631px;top:1296px;font-size:46px;line-height:43px}
.rule{position:absolute;height:2px;background:#d6d7db}
.about-lead{left:631px;top:1415px;width:360px;font-size:16px;line-height:19px}
.about-text{left:631px;width:340px;font-size:13.5px;line-height:21px;color:var(--text)}
.ghost-word{left:612px;top:1716px;font-size:150px;color:#f1f1f3;line-height:1}

/* gallery */
.gallery-band{left:0;top:1781px;width:920px;height:311px;background:var(--dark)}
.gallery-title{left:94px;top:1842px;font-size:44px;color:#fff}
.gallery-photo{top:1914px;width:327px;height:333px}

/* specs */
.spec-title{left:90px;top:2420px;font-size:84px;line-height:72px}
.spec-text{left:90px;top:2600px;width:420px;font-size:16px;line-height:20px}
.spec-disc{left:884px;top:2334px;width:466px;height:466px;border-radius:50%;background:var(--amber)}
.spec-vertical{left:1045px;top:2345px;font-size:98px;color:rgba(200,90,10,.45);writing-mode:vertical-rl;transform:rotate(180deg);line-height:1}
.spec-chair{left:578px;top:2316px;width:450px;height:500px;border-radius:40px 40px 60px 60px;background:linear-gradient(180deg,#3e4656 0%,#596273 45%,#d9dde3 70%,#2b2d33 100%)}

/* testimonials */
.test-title{left:0;top:2900px;width:1200px;text-align:center;font-size:44px}
.test-card{top:2970px;width:326px;height:268px;background:#fff;border-radius:26px;box-shadow:0 10px 30px rgba(0,0,0,.07);padding:26px 28px}
.quote-mark{font-family:'Bebas Neue',sans-serif;font-size:90px;line-height:60px;color:#e9eaed;height:44px}
.test-text{font-size:13.5px;line-height:22px;color:var(--text);margin-top:2px;height:68px}
.stars{margin-top:6px;display:flex;gap:2px}
.test-divider{height:1px;background:#e5e6ea;margin:16px 0 14px}
.person{display:flex;align-items:center;gap:10px}
.avatar{width:56px;height:56px;border-radius:50%;background:linear-gradient(135deg,#c7a58a,#6b4f3c)}
.person-name{font-family:'Bebas Neue',sans-serif;font-size:19px;color:var(--ink);line-height:1}
.person-role{font-size:13px;color:#8a8e96;margin-top:3px}

/* footer */
.footer{left:0;top:3332px;width:1200px;height:519px;background:var(--footer)}
.foot-brand{left:108px;top:3524px}
.foot-brand .brand-name{font-size:36px}
.foot-brand .brand-tag{font-size:13px;margin-top:4px}
.foot-head{font-size:23px;color:var(--ink)}
.contact-item{position:absolute;left:472px;display:flex;gap:20px}
.contact-item .ico{width:20px;padding-top:4px}
.contact-item h4{font-size:12px;font-weight:600;color:var(--ink)}
.contact-item p{font-size:13.5px;line-height:20px;color:var(--text)}
.field-label{position:absolute;font-size:12px;font-weight:600;color:var(--ink)}
.field{position:absolute;background:#fff;border:1px solid #e3e4e8;font-size:12.5px;color:#9a9ea6;padding:0 17px;display:flex;align-items:center}
.field.area{align-items:flex-start;padding-top:14px}
.send{font-size:17px;letter-spacing:1px}
.foot-rule{left:90px;top:3795px;width:1020px;height:1px;background:var(--line)}
.copyright{left:106px;top:3811px;font-size:13px;font-weight:600;color:var(--ink)}
.social{left:1078px;top:3808px;width:27px;height:27px;border-radius:50%;background:#fff;box-shadow:0 2px 8px rgba(0,0,0,.1)}
.to-top{left:1132px;top:3774px;width:42px;height:42px;border-radius:50%;background:#15171b;display:flex;align-items:center;justify-content:center}
</style>
</head>
<body>

<header class="abs site-header">
  <div class="brand">
    <span class="brand-name">Kestrel Q8</span>
    <span class="brand-tag">6 WHEEL-DRIVE ELECTRIC WHEELCHAIR</span>
  </div>
  <nav class="nav">
    <span>HOME</span><span>SPECIFICATIONS</span><span>GALLERY</span><span>VIDEO</span><span>TESTIMONIALS</span>
    <span class="contact">CONTACT US</span>
    <svg class="user-icon" width="20" height="22" viewBox="0 0 20 22" fill="none" stroke="#1d1f24" stroke-width="1.6"><circle cx="10" cy="7" r="5"/><path d="M1 21c1-5 4.5-7.5 9-7.5s8 2.5 9 7.5"/></svg>
  </nav>
</header>

<div class="photo hero-photo" role="img" aria-label="Man driving the six-wheel wheelchair across a stony riverbed"></div>
<h1 class="abs display hero-title">TAKE<br>YOUR SELF PLACES<br>OTHER <span class="accent">WHEELCHAIRS</span><br>CAN NOT GO</h1>
<p class="abs hero-text">The Kestrel Q8 wheelchair is an all-terrain off-road electric wheelchair made for the outdoors...</p>
<a class="btn" style="left:90px;top:505px;width:128px;height:39px">Read More</a>
<div class="abs hero-count">01 <small>/ 05</small></div>

<section>
  <div class="abs ideal-band"></div>
  <h2 class="abs display ideal-title">6 WHEEL DRIVE ELECTRIC WHEEL CHAIR IS IDEAL FOR:</h2>
  <div class="dot-grid" style="left:108px;top:842px;grid-template-columns:repeat(3,9px);gap:20px 19px">
    <span></span><span></span><span></span><span></span><span></span><span></span><span></span><span></span><span style="visibility:hidden"></span><span></span><span></span>
  </div>
  <div class="dot-grid" style="left:1006px;top:1048px;grid-template-columns:repeat(3,9px);gap:19px 19px">
    <span style="visibility:hidden"></span><span style="visibility:hidden"></span><span></span>
    <span style="visibility:hidden"></span><span style="visibility:hidden"></span><span></span>
    <span></span><span></span><span></span>
    <span></span><span></span><span></span>
  </div>
  <div class="abs use-card" style="left:160px"><div class="icon" role="img" aria-label="Fishing icon"></div><span class="display label">FISHING</span></div>
  <div class="abs use-card" style="left:338px"><div class="icon" role="img" aria-label="Hunting icon"></div><span class="display label">HUNTING</span></div>
  <div class="abs use-card" style="left:516px"><div class="icon" role="img" aria-label="Lifestyle blocks icon"></div><span class="display label">LIFESTYLE BLOCKS</span></div>
  <div class="abs use-card" style="left:694px"><div class="icon" role="img" aria-label="Beach icon"></div><span class="display label">BEACH</span></div>
  <div class="abs use-card" style="left:872px"><div class="icon" role="img" aria-label="Bush icon"></div><span class="display label">BUSH</span></div>
</section>

<section>
  <div class="abs display ghost-word">WHEELCHAIR</div>
  <div class="photo video-photo" role="img" aria-label="Rider climbing coastal rocks in the wheelchair by the sea"></div>
  <div class="abs play"><svg width="20" height="22" viewBox="0 0 20 22"><path d="M2 1l17 10L2 21z" fill="#fff"/></svg></div>
  <h2 class="abs display about-title">THE KESTREL Q8<br>WHEELCHAIR</h2>
  <div class="rule" style="left:631px;top:1393px;width:36px"></div>
  <p class="abs display about-lead">THE KESTREL Q8 WHEELCHAIR IS AN ALL-TERRAIN OFF-ROAD ELECTRIC WHEELCHAIR MADE FOR THE OUTDOORS...</p>
  <p class="abs about-text" style="top:1471px">Ideal for farms, bush, on the beach, lifestyle blocks, hunting, fishing.</p>
  <p class="abs about-text" style="top:1521px">This ultimate 6-wheel-drive outdoor electric wheelchair will take you places other wheel chairs and mobility scooters will not go.</p>
</section>

<section>
  <div class="abs gallery-band"></div>
  <h2 class="abs display gallery-title">OUR GALLERY</h2>
  <div class="photo gallery-photo" style="left:94px;background:linear-gradient(180deg,#c9d4da,#6a625a)" role="img" aria-label="Couple seated on the wheelchair on a driftwood beach"></div>
  <div class="photo gallery-photo" style="left:430px;background:linear-gradient(180deg,#a9c9e4,#8d8f92 60%,#5b5a58)" role="img" aria-label="Rider on the wheelchair on a dark sand beach"></div>
  <div class="photo gallery-photo" style="left:766px;background:linear-gradient(180deg,#b9c5cc,#9d9891 55%,#7c776f)" role="img" aria-label="Rider on the wheelchair on a pebble shore"></div>
  <div class="photo gallery-photo" style="left:1103px;width:97px;background:linear-gradient(180deg,#7f9a63,#5a6b4a)" role="img" aria-label="Rider on the wheelchair in the bush"></div>
</section>

<section>
  <div class="abs spec-disc"></div>
  <div class="abs display spec-vertical">WHEELCHAIR</div>
  <div class="photo spec-chair" role="img" aria-label="Studio shot of the six-wheel electric wheelchair with black seat and silver frame"></div>
  <h2 class="abs display spec-title">OUR<br>SPECIFICATIONS</h2>
  <div class="rule" style="left:235px;top:2464px;width:313px"></div>
  <div class="rule" style="left:90px;top:2578px;width:36px"></div>
  <p class="abs display spec-text">CHECK OUT THE DETAILED SPECIFICATIONS OF THE KESTREL Q8. SEE WHAT MAKES IT YOUR BEST TRAVEL COMPANION!</p>
  <a class="btn" style="left:90px;top:2664px;width:154px;height:38px">Specifications</a>
</section>

<section>
  <h2 class="abs display test-title">CLIENT’S TESTIMONIAL</h2>
  <article class="abs test-card" style="left:90px">
    <div class="quote-mark">“</div>
    <p class="test-text">Dr. Marcelo é super ético e atencioso. Esclareceu todas as dúvidas e estou muito satisfeita.</p>
    <div class="stars"><svg width="96" height="18" viewBox="0 0 96 18"><g fill="var(--amber)"><path id="st" d="M9 1l2.4 5 5.4.6-4 3.7 1.1 5.4L9 13l-4.9 2.7 1.1-5.4-4-3.7 5.4-.6z"/><use href="#st" x="19"/><use href="#st" x="38"/><use href="#st" x="57"/></g><use href="#st" x="76" fill="#f6d9a8"/></svg></div>
    <div class="test-divider"></div>
    <div class="person"><div class="avatar" role="img" aria-label="Client portrait"></div><div><div class="person-name">LENA FERRAZ</div><div class="person-role">Explorer</div></div></div>
  </article>
  <article class="abs test-card" style="left:436px">
    <div class="quote-mark">“</div>
    <p class="test-text">Atendimento de qualidade, dr Marcelo muito atencioso, diálogo claro. Pontualidade e..</p>
    <div class="stars"><svg width="96" height="18" viewBox="0 0 96 18"><g fill="var(--amber)"><use href="#st"/><use href="#st" x="19"/><use href="#st" x="38"/><use href="#st" x="57"/></g><use href="#st" x="76" fill="#f6d9a8"/></svg></div>
    <div class="test-divider"></div>
    <div class="person"><div class="avatar" role="img" aria-label="Client portrait"></div><div><div class="person-name">CLARA VIDAL</div><div class="person-role">Explorer</div></div></div>
  </article>
  <article class="abs test-card" style="left:784px">
    <div class="quote-mark">“</div>
    <p class="test-text">Por enquanto fiz apenas a consulta. Muita atenção e respeito por parte de todos os profissionais da clínica</p>
    <div class="stars"><svg width="96" height="18" viewBox="0 0 96 18"><g fill="var(--amber)"><use href="#st"/><use href="#st" x="19"/><use href="#st" x="38"/><use href="#st" x="57"/></g><use href="#st" x="76" fill="#f6d9a8"/></svg></div>
    <div class="test-divider"></div>
    <div class="person"><div class="avatar" role="img" aria-label="Client portrait"></div><div><div class="person-name">TOMAS REIS</div><div class="person-role">Explorer</div></div></div>
  </article>
</section>

<footer>
  <div class="abs footer"></div>
  <div class="abs brand foot-brand">
    <span class="brand-name">Kestrel Q8</span>
    <span class="brand-tag">6 WHEEL-DRIVE ELECTRIC WHEELCHAIR</span>
  </div>

  <h3 class="abs display foot-head" style="left:472px;top:3410px">CONTACT US</h3>
  <div class="contact-item" style="top:3452px">
    <div class="ico"><svg width="12" height="16" viewBox="0 0 12 16"><path d="M6 0a6 6 0 016 6c0 4.5-6 10-6 10S0 10.5 0 6a6 6 0 016-6z" fill="var(--orange)"/><circle cx="6" cy="6" r="2.2" fill="#fff"/></svg></div>
    <div><h4>LOCATION*</h4><p>PO Box 418 . Kaiwaka .<br>Northland New Zealand</p></div>
  </div>
  <div class="contact-item" style="top:3530px">
    <div class="ico"><svg width="14" height="14" viewBox="0 0 14 14"><path d="M3 0l3 3-2 2c1 2 3 4 5 5l2-2 3 3-2 3C6 14 0 8 0 3z" fill="var(--orange)"/></svg></div>
    <div><h4>PHONE*</h4><p>+64 9 555 0192.</p></div>
  </div>
  <div class="contact-item" style="top:3589px">
    <div class="ico"><svg width="14" height="11" viewBox="0 0 14 11"><rect width="14" height="11" rx="1.5" fill="var(--orange)"/><path d="M1 1.5l6 4.5 6-4.5" stroke="#fff" stroke-width="1.3" fill="none"/></svg></div>
    <div><h4>EMAIL*</h4><p>dale@kestrelq8.co.nz.</p></div>
  </div>

  <h3 class="abs display foot-head" style="left:733px;top:3410px">GET IN TOUCH</h3>
  <span class="field-label" style="left:733px;top:3447px">Name*</span>
  <span class="field-label" style="left:919px;top:3447px">Email*</span>
  <div class="field" style="left:733px;top:3466px;width:175px;height:36px">Enter your name</div>
  <div class="field" style="left:919px;top:3466px;width:175px;height:36px">Enter your email</div>
  <span class="field-label" style="left:733px;top:3512px">Phone*</span>
  <div class="field" style="left:733px;top:3532px;width:361px;height:36px">Enter phone number</div>
  <span class="field-label" style="left:733px;top:3578px">Inquiry*</span>
  <div class="field area" style="left:733px;top:3597px;width:361px;height:96px">Type your text</div>
  <a class="btn send" style="left:735px;top:3716px;width:99px;height:36px">SEND</a>

  <div class="abs foot-rule"></div>
  <p class="abs copyright">COPYRIGHT © 2021 ALL RIGHTS RESERVED</p>
  <a class="abs social" aria-label="Our social page"></a>
  <a class="abs to-top" aria-label="Back to top"><svg width="12" height="14" viewBox="0 0 12 14" fill="none" stroke="#fff" stroke-width="1.5"><path d="M6 13V1M1 6l5-5 5 5"/></svg></a>
</footer>

</body>
</html>
```